Web Design Project

We have a website in beta that needs updating and are looking for a freash new look for the Home page including Logo.
Our company is called " Kip Dorra " we specialize in classified advertising using video. Our consumers will be businesses selling a product or service. Please visit www.kipdorra.com
Our aim past this point is to engage a developer to write the code based on the best design. Our target market is the U.S and I have included some of the landing pages to give you a better idea of what we are trying to acheive

http://www.kipdorra.com/
http://www.kipdorra.com/cars_home.php
http://www.kipdorra.com/boats.php
http://www.kipdorra.com/electronic.php
http://www.kipdorra.com/realestate.php
http://www.kipdorra.com/roommates.php
Updates

Target Market(s)

20-35 yr old people who are connected to the internet via mobile phone and use social media on a daily/weekly basis

Industry/Entity Type

Advertising

Requirements
Must have
• We would like to use lots of images to convey it is a video driven website business
Nice to have
• Logo to incorporate same theme of website ( ie ) you are here to watch videos of thinhs to buy & sell
Should not have
• This is to be a freash new site with large type and bold fonts

```html
<!DOCTYPE html>
<html lang="en">
<head>
<meta charset="utf-8">
<title>Kip Dorra – Video Classifieds</title>
<link href="https://fonts.googleapis.com/css2?family=Ubuntu:wght@400;500&display=swap" rel="stylesheet">
<style>
:root{
  --red-deep:#9e1c0e;
  --red:#b92b17;
  --red-bright:#d9532a;
  --heading:#a8200f;
  --yellow:#f8c800;
  --yellow-text:#b5310c;
  --page:#f2f2f2;
  --band:#ebebeb;
  --footer:#e9e9e9;
  --ink:#333;
  --muted:#8a8a8a;
  --white:#fff;
}
*{box-sizing:border-box;margin:0;padding:0}
html,body{width:976px;height:1200px;overflow:hidden}
body{font-family:"Ubuntu",sans-serif;background:var(--page);position:relative;color:var(--ink)}
.abs{position:absolute}

.topbar{left:0;top:0;width:976px;height:37px;background:linear-gradient(var(--red-bright),var(--red-deep))}
.lang-label{left:514px;top:12px;font-size:9px;color:var(--white)}
.lang-select{left:605px;top:7px;width:87px;height:24px;background:#a72313;border:1px solid #8e1a0c;display:flex;align-items:center;gap:5px;padding-left:6px;font-size:9px;color:var(--white)}
.lang-flag{width:21px;height:12px;background:linear-gradient(#2b3f8e,#c8102e)}
.lang-caret{margin-left:auto;margin-right:8px;width:0;height:0;border-left:4px solid transparent;border-right:4px solid transparent;border-top:6px solid #ddd}
.btn{top:7px;height:24px;background:var(--yellow);color:var(--yellow-text);font-size:10px;display:flex;align-items:center;justify-content:center}
.btn-create{left:698px;width:83px}
.btn-signin{left:787px;width:83px}

.brand-name{left:106px;top:58px;font-size:28px;font-weight:500;color:var(--red);line-height:32px}
.brand-tag{left:106px;top:100px;font-size:10px;color:#444;line-height:13px}
.brand-tag b{font-size:14px;font-weight:500}

.nav{left:106px;top:144px;width:764px;height:59px;background:linear-gradient(var(--red-bright),var(--red-deep));display:flex;align-items:center}
.nav-item{height:59px;display:flex;align-items:center;justify-content:center;color:var(--white);font-size:13.5px;border-right:1px solid #a52210}
.search{left:660px;top:163px;width:200px;height:21px;background:var(--white);border:1px solid #ccc;font-size:7px;color:#aaa;padding:6px 6px}
.search svg{position:absolute;right:5px;top:4px}

.hero-photo{left:106px;top:236px;width:382px;height:195px;background:radial-gradient(ellipse at 55% 55%,#c81e1e 0 30%,#eee 62%,var(--page) 75%)}
.video-frame{left:499px;top:236px;width:309px;height:181px;background:var(--white);box-shadow:0 1px 4px rgba(0,0,0,.2)}
.video-still{left:506px;top:242px;width:296px;height:170px;background:linear-gradient(#8a8f93,#4a4d52 55%,#6d6f72)}
.play-big{left:623px;top:300px;width:59px;height:34px;background:rgba(20,20,20,.8);border-radius:3px}
.video-bar{left:516px;top:386px;width:278px;height:19px;background:rgba(20,20,20,.75)}
.video-progress{left:568px;top:394px;width:105px;height:3px;background:#d11}
.dots{left:804px;top:436px;display:flex;gap:3px}
.dot{width:9px;height:9px;border-radius:50%;background:#888}
.dot.on{background:var(--red)}

.welcome{left:0;top:474px;width:976px;height:143px;background:var(--band)}
.section-title{width:976px;text-align:center;font-size:18px;color:var(--heading)}
.welcome-copy{left:113px;top:546px;width:750px;text-align:center;font-size:10px;line-height:19.5px;color:var(--muted)}

.steps{left:0;top:617px;width:976px;height:306px;background:var(--page)}
.step{top:671px;width:194px;height:194px;border-radius:50%;background:linear-gradient(var(--red-bright),var(--red-deep))}
.step svg{position:absolute;left:57px;top:40px}
.step-label{position:absolute;top:135px;width:194px;text-align:center;color:var(--white);font-size:18px}

.footer{left:0;top:923px;width:976px;height:277px;background:var(--footer)}
.col-head{top:952px;font-size:14px;font-weight:500;color:var(--heading)}
.col-icon{top:950px}
.links{top:993px;font-size:10.5px;line-height:19.5px;color:var(--ink);list-style:none}
.social{top:983px;left:758px;width:100px;font-size:10.5px;list-style:none}
.social li{display:flex;justify-content:space-between;align-items:center;height:39px}
.social-mark{width:18px;height:18px;border-radius:50%;background:#111}
.rule{left:16px;top:1148px;width:960px;height:1px;background:#d6d6d6}
.copyright{left:0;top:1162px;width:952px;text-align:center;font-size:10.5px;color:#444}
</style>
</head>
<body>

<header>
  <div class="abs topbar"></div>
  <span class="abs lang-label">Select your Language</span>
  <div class="abs lang-select"><span class="lang-flag" role="img" aria-label="English flag"></span>English<span class="lang-caret"></span></div>
  <a class="abs btn btn-create">Create an Ad</a>
  <a class="abs btn btn-signin">Sign In</a>

  <span class="abs brand-name">Kip Dorra</span>
  <p class="abs brand-tag">Buy and sell through the<br><b>#1 Video Classifieds</b></p>

  <nav class="abs nav">
    <a class="nav-item" style="width:65px">Cars</a>
    <a class="nav-item" style="width:65px">Boats</a>
    <a class="nav-item" style="width:90px">Electronics</a>
    <a class="nav-item" style="width:91px">Real Estate</a>
    <a class="nav-item" style="width:86px">Roomates</a>
    <a class="nav-item" style="width:131px">Other Categories</a>
  </nav>
  <div class="abs search">Type search
    <svg width="12" height="12" viewBox="0 0 12 12"><circle cx="5" cy="5" r="3.5" fill="none" stroke="#aaa" stroke-width="1.2"/><path d="M7.5 7.5l3 3" stroke="#aaa" stroke-width="1.5"/></svg>
  </div>
</header>

<section>
  <div class="abs hero-photo" role="img" aria-label="Red sedan car on a white background"></div>
  <div class="abs video-frame"></div>
  <div class="abs video-still" role="img" aria-label="Video still of a black coupe in a parking lot"></div>
  <div class="abs play-big"><svg width="59" height="34"><path d="M25 10l12 7-12 7z" fill="#fff"/></svg></div>
  <div class="abs video-bar"><svg width="30" height="19"><path d="M12 5l7 4.5-7 4.5z" fill="#fff"/></svg></div>
  <div class="abs video-progress"></div>
  <div class="abs dots"><span class="dot on"></span><span class="dot"></span><span class="dot"></span><span class="dot"></span></div>
</section>

<section class="abs welcome">
  <h1 class="abs section-title" style="top:33px;font-weight:400">Welcome to Kip Dorra</h1>
</section>
<p class="abs welcome-copy">Lorem Ipsum is simply dummy text of the printing and typesetting industry. Lorem Ipsum has been the industry's standard dummy text ever since the 1500s, when an unknown printer took a galley of type and scrambled it to make a type specimen book.</p>

<section class="abs steps">
  <h2 class="abs section-title" style="top:17px;font-weight:400">How it works</h2>
</section>
<div class="abs step" style="left:131px">
  <svg width="80" height="70" viewBox="0 0 80 70"><g fill="#fff" transform="translate(40 32)"><rect x="-30" y="-7" width="60" height="14" transform="rotate(45)"/><rect x="-30" y="-7" width="60" height="14" transform="rotate(-45)"/></g></svg>
  <span class="step-label">Create It</span>
</div>
<div class="abs step" style="left:390px">
  <svg width="90" height="70" viewBox="0 0 90 70" style="left:52px"><path d="M0 30l15-25h60l15 25v30a5 5 0 0 1-5 5H5a5 5 0 0 1-5-5z" fill="#fff"/><path d="M8 30h20l5 10h24l5-10h20l-10-18H18z" fill="#c23b1c"/><path d="M45 8l-10 11h6v12h8V19h6z" fill="#fff"/></svg>
  <span class="step-label">Upload It</span>
</div>
<div class="abs step" style="left:654px">
  <svg width="90" height="70" viewBox="0 0 90 70" style="left:50px"><g fill="#fff"><rect x="30" y="2" width="58" height="6"/><rect x="30" y="12" width="58" height="6"/><rect x="30" y="22" width="58" height="6"/><rect x="30" y="32" width="58" height="6"/><rect x="30" y="42" width="58" height="6"/><rect x="30" y="52" width="58" height="6"/><circle cx="23" cy="44" r="22"/></g><text x="23" y="53" text-anchor="middle" font-family="Ubuntu,sans-serif" font-size="28" font-weight="500" fill="#c23b1c">$</text></svg>
  <span class="step-label">Sell It</span>
</div>

<footer>
  <div class="abs footer"></div>

  <svg class="abs col-icon" style="left:134px" width="26" height="26" viewBox="0 0 26 26"><circle cx="10" cy="10" r="7.5" fill="none" stroke="#444" stroke-width="2.5"/><path d="M15.5 15.5l8 8" stroke="#444" stroke-width="3.5"/></svg>
  <span class="abs col-head" style="left:170px">Buy / Browse</span>
  <ul class="abs links" style="left:170px"><li>Roommates</li><li>Cars</li><li>Boats</li><li>Electronics</li><li>Others</li></ul>

  <svg class="abs col-icon" style="left:326px" width="32" height="22" viewBox="0 0 32 22"><rect x="1" y="5" width="27" height="15" fill="none" stroke="#444" stroke-width="2"/><rect x="4" y="2" width="27" height="15" fill="none" stroke="#444" stroke-width="1.5"/><circle cx="14" cy="12.5" r="4" fill="#444"/></svg>
  <span class="abs col-head" style="left:366px">Sell</span>
  <ul class="abs links" style="left:366px"><li>Start Selling</li><li>Login</li><li>Shooting Video</li><li>Uploading</li><li>Video Buying</li></ul>

  <svg class="abs col-icon" style="left:461px" width="22" height="22" viewBox="0 0 22 22"><circle cx="11" cy="11" r="11" fill="#444"/><rect x="9.5" y="9" width="3" height="8" fill="#fff"/><circle cx="11" cy="6" r="1.8" fill="#fff"/></svg>
  <span class="abs col-head" style="left:496px">Info</span>
  <ul class="abs links" style="left:496px"><li>Blog</li><li>FAQs</li><li>Terms of Use</li><li>Privacy Policy</li><li>Buyer/Seller</li><li>&nbsp;Safety</li></ul>

  <svg class="abs col-icon" style="left:603px" width="18" height="26" viewBox="0 0 18 26"><path d="M4 1l4 6-3 3c1 4 3 8 6 10l3-2 4 5-3 2C8 25 0 13 1 4z" fill="#444"/></svg>
  <span class="abs col-head" style="left:626px">Contact</span>
  <ul class="abs links" style="left:626px"><li>Contact Us</li><li>Feedback</li><li>Form</li><li>Referral Program</li><li>Business</li><li>Register</li><li>Subscription</li></ul>

  <svg class="abs col-icon" style="left:732px" width="22" height="22" viewBox="0 0 22 22"><path d="M2 20c0-8 5-12 12-12V3l7 7-7 7v-5c-6 0-9 2-12 8z" fill="#444"/></svg>
  <span class="abs col-head" style="left:758px">Connect With Us</span>
  <ul class="abs social">
    <li>Chirpline<span class="social-mark"></span></li>
    <li>Circlebook<span class="social-mark"></span></li>
    <li>RSS Feeder
      <svg width="22" height="22" viewBox="0 0 22 22"><circle cx="4" cy="18" r="3" fill="#111"/><path d="M1 9a12 12 0 0 1 12 12M1 2a19 19 0 0 1 19 19" fill="none" stroke="#111" stroke-width="3.5"/></svg>
    </li>
  </ul>

  <div class="abs rule"></div>
  <p class="abs copyright">©2013 Kip Dorra | All Rights Reserved</p>
</footer>

</body>
</html>
```